Template Flyer- Corewell Stretch & Flow

I am wanting a template 1 page flyer designed to use on the back ground of newsletter (faded background) and for our advertising posters in A4, A3, for Facebook and Instagram compatibility.

I have loaded an example from another Studio called Pinegrove (file 3)- each time they have a new workshop to advertise a picture is placed in the little circle (so this is something I would want to do too where I can load a new picture each time a new workshop is running)- They have used the flyer like a water mark...I like this.

Our colour palette is what is on our logos and you can also visit our website for a feel for what we like www.corewellstretch.com.au

I need some of the designs edited a bit more and because of the time difference, there seems to be a 24hour period where we communicate with each other. May I please request another 2 days extension

Requirements
Must have
• Id like to have a picture in the back ground. My favourite back ground that has been produced so far is a background of both picture file 9 and 10 in either.
Nice to have
• 3 picture circles options to advertise the events/workshops I have each year.
• Brush stroke style circles (see picture attached)rather then smooth circles for the picture area (in a grey tone)
Should not have
• No BLACK colour writing or black circles

```html
<!DOCTYPE html>
<html lang="en">
<head>
<meta charset="utf-8">
<title>Corewell Stretch &amp; Flow – 1 Day Retreat</title>
<link href="https://fonts.googleapis.com/css2?family=Jost:wght@400;500;600&display=swap" rel="stylesheet">
<style>
  :root {
    --teal: #1a89a6;
    --ink: #3b3d40;
    --muted: #8a8f93;
    --rule: #b9bcbf;
    --ring: #4a4c4f;
    --page: #ffffff;
    --stage: #e9eaeb;
  }
  * { margin: 0; padding: 0; box-sizing: border-box; }
  html, body { width: 1200px; height: 1200px; overflow: hidden; background: var(--stage); }
  body { font-family: "Jost", "Century Gothic", sans-serif; color: var(--ink); }

  .flyer {
    position: absolute; left: 190px; top: 22px;
    width: 794px; height: 1122px;
    transform: scale(1.03); transform-origin: top left;
    background: var(--page); overflow: hidden;
  }
  .backdrop {
    position: absolute; inset: 0;
    background: linear-gradient(100deg, #f6ede3 0%, #faf5ef 35%, #ffffff 70%);
  }
  .side-decor {
    position: absolute; right: 0; top: 0; width: 190px; height: 780px;
    background: linear-gradient(180deg, rgba(220,200,160,.25) 0%, rgba(140,220,225,.35) 50%, rgba(240,150,160,.4) 78%, rgba(255,255,255,0) 100%);
  }

  .brand { position: absolute; left: 0; right: 0; top: 70px; display: flex; justify-content: center; align-items: center; gap: 16px; }
  .brand-dot { width: 46px; height: 46px; border-radius: 50%; border: 4px solid var(--teal); }
  .brand-name { font-size: 40px; font-weight: 400; color: var(--teal); letter-spacing: .5px; }

  .photos { position: absolute; left: 0; top: 0; }

  .title-row { position: absolute; left: 37px; width: 719px; top: 668px; display: flex; align-items: center; gap: 14px; }
  .title-row::before, .title-row::after { content: ""; flex: 1; height: 1px; background: var(--rule); }
  .title-row::before { flex: 0 0 178px; }
  .title { font-size: 46px; font-weight: 600; color: var(--teal); letter-spacing: 1px; }

  .intro-box {
    position: absolute; left: 37px; top: 693px; width: 719px; height: 107px;
    border: 1px solid var(--rule); border-top: none; border-radius: 0 0 4px 4px;
  }
  .intro-box::before, .intro-box::after { content: ""; position: absolute; top: 0; width: 1px; height: 1px; }
  .intro { position: absolute; left: 49px; top: 722px; width: 696px; font-size: 17px; line-height: 22.5px; text-align: justify; }
  .intro b { font-weight: 600; }

  .when { position: absolute; left: 0; right: 0; top: 818px; text-align: center; font-size: 28px; font-weight: 600; color: var(--teal); letter-spacing: .3px; }
  .when .bar { color: var(--muted); font-weight: 400; padding: 0 6px; }
  .extras { position: absolute; left: 0; right: 0; top: 870px; text-align: center; font-size: 26px; font-weight: 400; }

  .cost-box { position: absolute; left: 159px; top: 940px; width: 476px; height: 87px; border: 1px solid var(--rule); border-radius: 4px; }
  .cost-label { position: absolute; left: 0; right: 0; top: 920px; text-align: center; }
  .cost-label span { background: #fff; padding: 0 10px; font-size: 25px; font-weight: 600; color: var(--teal); }
  .price { position: absolute; left: 0; right: 0; text-align: center; font-size: 26px; }
  .price b { color: var(--teal); font-weight: 600; }
  .price-full { top: 956px; }
  .price-conc { top: 988px; }

  .footer { position: absolute; left: 0; right: 0; top: 1040px; height: 82px; background: var(--page); font-size: 16.5px; }
  .footer .item { position: absolute; display: flex; align-items: center; gap: 8px; white-space: nowrap; }
  .footer svg { width: 15px; height: 15px; fill: none; stroke: var(--teal); stroke-width: 2; }
  .addr { left: 180px; top: 6px; }
  .phone { left: 36px; top: 35px; font-weight: 600; }
  .mail { left: 207px; top: 35px; }
  .web { left: 500px; top: 35px; }
</style>
</head>
<body>
<main class="flyer">
  <div class="backdrop" role="img" aria-label="Faded photo of a calm studio interior"></div>
  <div class="side-decor" role="img" aria-label="Hanging beaded strings with aqua and pink tassels"></div>

  <header class="brand">
    <span class="brand-dot"></span>
    <span class="brand-name">Corewell Stretch &amp; Flow</span>
  </header>

  <svg class="photos" width="794" height="660" viewBox="0 0 794 660">
    <circle cx="286" cy="404" r="190" fill="#c9cdb8" role="img" aria-label="Studio with yoga mats, bolsters and cork blocks"/>
    <circle cx="286" cy="404" r="196" fill="none" stroke="var(--ring)" stroke-width="9"/>
    <circle cx="288" cy="400" r="203" fill="none" stroke="var(--ring)" stroke-width="2" stroke-dasharray="40 14 22 8"/>
    <circle cx="548" cy="334" r="140" fill="#b9d9c4" role="img" aria-label="Pile of patterned yoga bolsters"/>
    <circle cx="548" cy="334" r="145" fill="none" stroke="var(--ring)" stroke-width="8"/>
    <circle cx="550" cy="331" r="151" fill="none" stroke="var(--ring)" stroke-width="2" stroke-dasharray="30 10 18 6"/>
  </svg>

  <div class="title-row"><h1 class="title">1 DAY RETREAT</h1></div>
  <div class="intro-box"></div>
  <p class="intro"><b>Facilitated by:</b> Tessa Marlow, Jodie Fenwick, Carla Ashby A weekend full of Inspiration, guided meditation, Yoga, Pilates, relaxation, philosophy, yummy nutritious food, and empowering information to live well in the world.</p>

  <p class="when">SATURDAY, 24th MARCH<span class="bar">|</span>10.00AM - 4.00PM</p>
  <p class="extras">LIGHT LUNCH &amp; SNACKS ARE INCLUDED</p>

  <div class="cost-box"></div>
  <p class="cost-label"><span>COST:</span></p>
  <p class="price price-full"><b>$120</b> PER PERSON</p>
  <p class="price price-conc"><b>$100</b> CONCESSION CARD HOLDERS</p>

  <footer class="footer">
    <div class="item addr">
      <svg viewBox="0 0 16 16"><path d="M8 15s5-5 5-9a5 5 0 0 0-10 0c0 4 5 9 5 9z"/><circle cx="8" cy="6" r="1.8"/></svg>
      18 Larkin St (5,531.68 mi), Ashvale, Victoria 3520
    </div>
    <div class="item phone">
      <svg viewBox="0 0 16 16"><path d="M4 1.5l2.5 3-1.5 2a8 8 0 0 0 4.5 4.5l2-1.5 3 2.5-1.5 2.5C7 14 2 9 1.5 3z"/></svg>
      (03) 5812 4469
    </div>
    <div class="item mail">
      <svg viewBox="0 0 16 16"><rect x="1.5" y="3.5" width="13" height="9"/><path d="M1.5 3.5L8 9l6.5-5.5"/></svg>
      info at corewellstretch.com.au
    </div>
    <div class="item web">
      <svg viewBox="0 0 16 16"><circle cx="8" cy="8" r="6.5"/><path d="M1.5 8h13M8 1.5c3 3.5 3 9.5 0 13M8 1.5c-3 3.5-3 9.5 0 13"/></svg>
      www.corewellstretch.com.au
    </div>
  </footer>
</main>
</body>
</html>
```